Email signature and business card

Australian company called Brakmere. We provide construction and maintenance services to the mining industry. I would like the design to be similar to our website theme(www.brakmere.com.au) whilst staying compact. RGB colours to include: 42,96,140 and 232,163,0 and I have attached 2 logos.

The following fields will need to be included:

Full Name
Title
Location/Project
Phone
Mobile
Fax
Email
Web site

Target Market(s)

Mining Industry

Industry/Entity Type

Construction

Requirements
Must have
• Full Name, Title, Office Address, Phone, Mobile, Fax, Email, Web address
• Back of card must include: Boilermaking, Carpentry, Concrete, Construction, Cranes, Data and Comms, Electrical, Fabrication, Fitting, Labour Hire, Plumbing, Rigging, Shutdowns

```html
<!DOCTYPE html>
<html lang="en">
<head>
<meta charset="utf-8">
<title>Brakmere – Business Card</title>
<link href="https://fonts.googleapis.com/css2?family=Open+Sans:wght@400;600;700;800&display=swap" rel="stylesheet">
<style>
  :root {
    --teal: #2a608c;
    --teal-dark: #1f4f73;
    --gold: #e8a300;
    --ink: #2b2b2b;
    --card: #ffffff;
    --stage: #e6e7e8;
  }
  * { box-sizing: border-box; margin: 0; padding: 0; }
  html, body { width: 1200px; height: 871px; overflow: hidden; }
  body {
    background: var(--stage);
    font-family: "Open Sans", Arial, sans-serif;
    position: relative;
  }
  .card {
    position: absolute;
    width: 620px;
    height: 354px;
    background: var(--card);
    border-radius: 4px;
    box-shadow: 0 6px 18px rgba(0,0,0,.18);
    overflow: hidden;
  }
  .card--back { left: 90px; top: 70px; }
  .card--front { left: 490px; top: 447px; }

  .brand {
    position: absolute;
    display: flex;
    flex-direction: column;
    align-items: center;
  }
  .brand__disc {
    border-radius: 50%;
    background: var(--teal);
  }
  .brand__name {
    font-weight: 800;
    color: var(--teal);
    letter-spacing: .5px;
  }
  .card--back .brand { left: 50px; top: 95px; width: 150px; }
  .card--back .brand__disc { width: 92px; height: 92px; margin-bottom: 12px; }
  .card--back .brand__name { font-size: 26px; }
  .brand__web { font-size: 12px; font-weight: 700; color: var(--teal); margin-top: 4px; }

  .services {
    position: absolute;
    top: 70px;
    display: flex;
    flex-direction: column;
    gap: 9px;
    list-style: none;
  }
  .services--a { left: 240px; }
  .services--b { left: 420px; }
  .services li {
    display: flex;
    align-items: center;
    gap: 10px;
    font-size: 15px;
    font-weight: 700;
    color: var(--teal);
  }
  .tick { width: 14px; height: 12px; flex: none; }

  .card--front .brand { left: 46px; top: 40px; width: 180px; }
  .card--front .brand__disc { width: 120px; height: 120px; margin-bottom: 14px; }
  .card--front .brand__name { font-size: 32px; }

  .contact {
    position: absolute;
    left: 300px;
    top: 70px;
    color: var(--ink);
  }
  .contact__name { font-size: 19px; font-weight: 700; color: var(--teal); letter-spacing: .5px; }
  .contact__title { font-size: 13px; margin-bottom: 14px; }
  .contact__company { font-size: 14px; font-weight: 700; color: var(--teal); }
  .contact__address { font-size: 13px; margin-bottom: 10px; }
  .contact__lines { list-style: none; display: flex; flex-direction: column; gap: 4px; }
  .contact__lines li { display: flex; align-items: center; gap: 12px; font-size: 13.5px; }
  .icon { width: 16px; height: 16px; flex: none; }

  .wave { position: absolute; left: 0; bottom: 0; width: 620px; height: 130px; }
</style>
</head>
<body>

<section class="card card--back" aria-label="Card back">
  <div class="brand">
    <div class="brand__disc"></div>
    <div class="brand__name">BRAKMERE</div>
    <div class="brand__web">www.brakmere.com</div>
  </div>

  <ul class="services services--a">
    <li><svg class="tick" viewBox="0 0 14 12"><path d="M1 6.5l4 4L13 1.5" fill="none" stroke="#e8a300" stroke-width="2.6"/></svg>Boilermaking</li>
    <li><svg class="tick" viewBox="0 0 14 12"><path d="M1 6.5l4 4L13 1.5" fill="none" stroke="#e8a300" stroke-width="2.6"/></svg>Carpentry</li>
    <li><svg class="tick" viewBox="0 0 14 12"><path d="M1 6.5l4 4L13 1.5" fill="none" stroke="#e8a300" stroke-width="2.6"/></svg>Concrete</li>
    <li><svg class="tick" viewBox="0 0 14 12"><path d="M1 6.5l4 4L13 1.5" fill="none" stroke="#e8a300" stroke-width="2.6"/></svg>Construction</li>
    <li><svg class="tick" viewBox="0 0 14 12"><path d="M1 6.5l4 4L13 1.5" fill="none" stroke="#e8a300" stroke-width="2.6"/></svg>Cranes</li>
    <li><svg class="tick" viewBox="0 0 14 12"><path d="M1 6.5l4 4L13 1.5" fill="none" stroke="#e8a300" stroke-width="2.6"/></svg>Data and Comms</li>
    <li><svg class="tick" viewBox="0 0 14 12"><path d="M1 6.5l4 4L13 1.5" fill="none" stroke="#e8a300" stroke-width="2.6"/></svg>Electrical</li>
  </ul>
  <ul class="services services--b">
    <li><svg class="tick" viewBox="0 0 14 12"><path d="M1 6.5l4 4L13 1.5" fill="none" stroke="#e8a300" stroke-width="2.6"/></svg>Fabrication</li>
    <li><svg class="tick" viewBox="0 0 14 12"><path d="M1 6.5l4 4L13 1.5" fill="none" stroke="#e8a300" stroke-width="2.6"/></svg>Fitting</li>
    <li><svg class="tick" viewBox="0 0 14 12"><path d="M1 6.5l4 4L13 1.5" fill="none" stroke="#e8a300" stroke-width="2.6"/></svg>Labour Hire</li>
    <li><svg class="tick" viewBox="0 0 14 12"><path d="M1 6.5l4 4L13 1.5" fill="none" stroke="#e8a300" stroke-width="2.6"/></svg>Plumbing</li>
    <li><svg class="tick" viewBox="0 0 14 12"><path d="M1 6.5l4 4L13 1.5" fill="none" stroke="#e8a300" stroke-width="2.6"/></svg>Rigging</li>
    <li><svg class="tick" viewBox="0 0 14 12"><path d="M1 6.5l4 4L13 1.5" fill="none" stroke="#e8a300" stroke-width="2.6"/></svg>Shutdowns</li>
  </ul>
</section>

<section class="card card--front" aria-label="Card front">
  <div class="brand">
    <div class="brand__disc"></div>
    <div class="brand__name">BRAKMERE</div>
  </div>

  <div class="contact">
    <div class="contact__name">Hanna Veld</div>
    <div class="contact__title">CEO</div>
    <div class="contact__company">Brakmere. Inc</div>
    <div class="contact__address">Lindenweg 14 CH - 6300 Kellbach</div>
    <ul class="contact__lines">
      <li><svg class="icon" viewBox="0 0 16 16"><path d="M2 5c0-2 2-3 6-3s6 1 6 3l-3 1-1-2H6L5 6 2 5zM4 8h8l1 6H3z" fill="none" stroke="#e8a300" stroke-width="1.4"/></svg>041 482 16 20</li>
      <li><svg class="icon" viewBox="0 0 16 16"><rect x="4" y="1" width="8" height="14" rx="1.5" fill="none" stroke="#e8a300" stroke-width="1.4"/><circle cx="8" cy="12.5" r="1" fill="#e8a300"/></svg>041 482 16 20</li>
      <li><svg class="icon" viewBox="0 0 16 16"><rect x="4" y="1.5" width="8" height="4" fill="none" stroke="#e8a300" stroke-width="1.4"/><rect x="1.5" y="5.5" width="13" height="6" rx="1" fill="none" stroke="#e8a300" stroke-width="1.4"/><rect x="4" y="10" width="8" height="4.5" fill="#fff" stroke="#e8a300" stroke-width="1.4"/></svg>041 482 16 21</li>
      <li><svg class="icon" viewBox="0 0 16 16"><rect x="1.5" y="3.5" width="13" height="9" fill="none" stroke="#e8a300" stroke-width="1.4"/><path d="M1.5 3.5L8 9l6.5-5.5" fill="none" stroke="#e8a300" stroke-width="1.4"/></svg>hanna@brakmere.com</li>
    </ul>
  </div>

  <svg class="wave" viewBox="0 0 620 130" preserveAspectRatio="none" aria-hidden="true">
    <path d="M0 20 C 180 20, 420 40, 620 118 L620 130 L0 130 Z" fill="#e8a300"/>
    <path d="M0 30 C 180 30, 420 52, 620 128 L620 130 L0 130 Z" fill="#ffffff"/>
    <path d="M0 36 C 180 40, 420 70, 620 130 L0 130 Z" fill="#2a608c"/>
  </svg>
</section>

</body>
</html>
```